Investment company needing business card

We are wanting a business card which looks sharp and easy on the eye. We are thinking of having a business card with the logo embossed on it, to really make it stand out. We will only have a small amount of information of the business card, person's name, position, email address and phone number

Contact Information for Business Card

Danielle Frost
Executive Assistant
+64 21 473 5162
danielf@harwickpartners.co.nz

Requirements
Must have
• Embossed logo
Should not have
• Not to be busy

```html
<!DOCTYPE html>
<html lang="en">
<head>
<meta charset="utf-8">
<title>Harwick Partners – Business Card</title>
<link rel="stylesheet" href="https://fonts.googleapis.com/css2?family=Montserrat:wght@500;700&family=Open+Sans:wght@400&display=swap">
<style>
  :root {
    --backdrop: #e8e5e2;
    --card: #ffffff;
    --brand-green: #22a867;
    --ink-grey: #4a4a4a;
    --soft-grey: #5c5c5c;
    --rule-grey: #8a8a8a;
  }
  * { box-sizing: border-box; margin: 0; padding: 0; }
  html, body {
    width: 1200px; height: 997px; overflow: hidden;
    background: var(--backdrop);
  }
  .sheet {
    position: relative; width: 1200px; height: 997px;
    display: flex; align-items: center; justify-content: center; gap: 40px;
  }
  .card {
    width: 540px; height: 309px;
    background: var(--card);
    box-shadow: 0 2px 8px rgba(0,0,0,0.08);
    position: relative;
  }
  /* contact side */
  .card--contact { display: flex; align-items: center; padding-left: 52px; }
  .contact__brand {
    display: flex; align-items: center; gap: 10px;
    font-family: "Montserrat", sans-serif; font-weight: 700;
    font-size: 22px; color: var(--brand-green); letter-spacing: 1px;
    width: 170px;
  }
  .brand-square { width: 16px; height: 16px; background: var(--brand-green); flex: none; }
  .contact__divider {
    width: 1px; height: 96px; background: var(--brand-green);
    margin: 0 26px 0 10px;
  }
  .contact__details { font-family: "Open Sans", sans-serif; color: var(--soft-grey); }
  .contact__name {
    font-family: "Montserrat", sans-serif; font-weight: 700;
    font-size: 16px; color: var(--brand-green); letter-spacing: 0.5px;
  }
  .contact__role { font-size: 13px; margin-bottom: 8px; }
  .contact__line { display: flex; align-items: center; gap: 8px; font-size: 12.5px; line-height: 19px; }
  .contact__line svg { width: 11px; height: 11px; flex: none; fill: var(--brand-green); }
  /* logo side */
  .card--brand { display: flex; align-items: center; justify-content: center; }
  .brand-lockup { display: flex; align-items: center; gap: 14px; }
  .brand-lockup .brand-square { width: 40px; height: 40px; }
  .brand-lockup__words { display: flex; flex-direction: column; align-items: center; }
  .brand-lockup__name {
    font-family: "Montserrat", sans-serif; font-weight: 700;
    font-size: 34px; color: var(--brand-green); letter-spacing: 2px; line-height: 1;
  }
  .brand-lockup__sub {
    display: flex; align-items: center; gap: 10px; margin-top: 6px;
    font-family: "Montserrat", sans-serif; font-weight: 500;
    font-size: 12px; letter-spacing: 5px; color: var(--ink-grey);
  }
  .brand-lockup__sub::before, .brand-lockup__sub::after {
    content: ""; width: 70px; height: 1px; background: var(--rule-grey);
  }
</style>
</head>
<body>
<main class="sheet">
  <section class="card card--contact">
    <div class="contact__brand"><span class="brand-square"></span>HARWICK</div>
    <div class="contact__divider"></div>
    <div class="contact__details">
      <p class="contact__name">DANIELLE FROST</p>
      <p class="contact__role">Executive Assistant</p>
      <p class="contact__line">
        <svg viewBox="0 0 24 24"><path d="M6.6 10.8a15 15 0 0 0 6.6 6.6l2.2-2.2a1 1 0 0 1 1-.25 11.4 11.4 0 0 0 3.6.57 1 1 0 0 1 1 1V20a1 1 0 0 1-1 1A17 17 0 0 1 3 4a1 1 0 0 1 1-1h3.5a1 1 0 0 1 1 1c0 1.25.2 2.45.57 3.57a1 1 0 0 1-.25 1z"/></svg>
        +64 21 473 5162
      </p>
      <p class="contact__line">
        <svg viewBox="0 0 24 24"><path d="M2 5h20v14H2z M2 5l10 8 10-8" fill="none" stroke="#22a867" stroke-width="2.5"/></svg>
        danielf@harwickpartners.co.nz
      </p>
      <p class="contact__line">
        <svg viewBox="0 0 24 24"><circle cx="12" cy="12" r="9" fill="none" stroke="#22a867" stroke-width="2.5"/><path d="M3 12h18M12 3c3 3 3 15 0 18M12 3c-3 3-3 15 0 18" fill="none" stroke="#22a867" stroke-width="2"/></svg>
        www.harwickpartners.co.nz
      </p>
    </div>
  </section>
  <section class="card card--brand">
    <div class="brand-lockup">
      <span class="brand-square"></span>
      <div class="brand-lockup__words">
        <span class="brand-lockup__name">HARWICK</span>
        <span class="brand-lockup__sub">PARTNERS</span>
      </div>
    </div>
  </section>
</main>
</body>
</html>
```